Upstart Retirement Planning Firm needs help with business card design

Harborview Nest Advisors, LLC is looking for help with business card design. We give advice on investments, insurance, and other financial matters related to retirement. There are some required disclosures that we will provide but mostly we are looking for a professional, classy business card that reflects the theme we have chosen. We have a logo that is attached but we would like to add a phrase; "Turning Your Earned Income Into Retirement Income"

Doubled sided only so that we can add the required disclosures (needed for our industry) on the back of the card. We will provide the exact words for this in 1-2 days.

Target Market(s)

Retirees and Pre-retirees. Professionals 50+ years old

Industry/Entity Type

Financial Planning

Contact Information for Business Card

We currently have two people who will need separate cards so we'd like to have a template so that we can add names for new cards in the future.

For the first run, please show the following information.

Gregor Pelham, MBA, ChFC®, CLU®
Financial Advisor, Registered Representative
gpelham@harborviewnest.example
Phone: (555) 318-2946
Toll Free Fax: (800) 555-0193

Address is
2187 Meadowlark Ridge Rd.
Suite K418
Virginia Beach, VA 23999

Colors
3277b5

Requirements
Must have
• Logo, contact info, small phase to describe business (in description), required legal disclosures on back of the card as follows (in small font)
• Gregor Pelham is a registered representative of and offers securities through Brightmoor Capital Brokerage Corporation, Member FNQX. Brightmoor Capital Brokerage Corporation is a member of the Brightmoor Capital Alliance which is the marketing name for Brightmoor Holding Corporation and its affiliates.
Nice to have
• Rounded edges, raised letters
Should not have
• any colors that aren't in the logo (other than black for font)

```html
<!DOCTYPE html>
<html lang="en">
<head>
<meta charset="utf-8">
<title>Harborview Nest Advisors – Business Card</title>
<link rel="stylesheet" href="https://fonts.googleapis.com/css2?family=Source+Sans+3:wght@400;600&display=swap">
<style>
  :root {
    --brand-blue: #2c5699;
    --brand-blue-soft: #3a64a6;
    --brand-grey: #9c9c9c;
    --paper: #ffffff;
    --backdrop: #e9e9eb;
    --ink-light: #ffffff;
    --ink-muted: rgba(255,255,255,0.85);
  }
  * { box-sizing: border-box; margin: 0; padding: 0; }
  html, body {
    width: 1200px; height: 900px; overflow: hidden;
    background: var(--backdrop);
    font-family: "Source Sans 3", "Myriad Pro", sans-serif;
  }
  .canvas { position: relative; width: 1200px; height: 900px; }

  .card {
    position: absolute;
    width: 556px; height: 342px;
    border-radius: 14px;
    overflow: hidden;
    box-shadow: 0 6px 18px rgba(0,0,0,0.18);
  }
  .card--front { left: 238px; top: 62px; background: var(--paper); }
  .card--back  { left: 459px; top: 518px; background: var(--brand-blue); }

  .card__wave { position: absolute; inset: 0; }

  .brand-name {
    position: absolute; left: 30px; top: 26px;
    color: var(--brand-blue);
    font-weight: 600;
    line-height: 1.02;
    font-size: 38px;
    letter-spacing: 0.3px;
  }
  .brand-name small { display: block; font-size: 17px; letter-spacing: 2.2px; margin-top: 6px; }

  .contact {
    position: absolute; right: 278px; top: 206px;
    text-align: right; color: var(--ink-light);
    font-size: 15px; line-height: 24px;
  }
  .contact__fax { font-weight: 600; }
  .contact__row { display: flex; justify-content: flex-end; align-items: center; gap: 8px; }
  .contact__icon { width: 11px; height: 11px; fill: var(--ink-light); }

  .person {
    position: absolute; left: 300px; top: 204px;
    color: var(--ink-light);
  }
  .person__name { font-size: 20px; font-weight: 600; line-height: 26px; }
  .person__name span { font-size: 14px; }
  .person__role { font-size: 15px; line-height: 21px; }

  .rule-line {
    position: absolute; left: 0; right: 0;
    display: flex; align-items: center; gap: 12px;
    color: var(--ink-light); font-size: 15px; white-space: nowrap;
  }
  .rule-line::before, .rule-line::after {
    content: ""; flex: 1; height: 1px; background: rgba(255,255,255,0.6);
  }
  .card--front .rule-line { top: 302px; }
  .card--back .rule-line { top: 293px; font-weight: 600; font-size: 15.5px; }
  .card--back .rule-line::before { flex: 0 0 76px; }
  .card--back .rule-line::after { flex: 0 0 82px; }

  .back-mark {
    position: absolute; left: 0; right: 0; top: 34px;
    text-align: center;
    color: var(--brand-blue-soft);
    font-weight: 600;
    font-size: 54px; line-height: 1.05;
  }

  .disclosure {
    position: absolute; left: 44px; right: 44px; top: 196px;
    color: var(--ink-muted);
    font-size: 10.5px; line-height: 14px;
    text-align: center;
  }
</style>
</head>
<body>
<main class="canvas">

  <section class="card card--front" aria-label="Business card front">
    <svg class="card__wave" viewBox="0 0 556 342" preserveAspectRatio="none" aria-hidden="true">
      <path d="M0 198 C180 188 380 130 556 92 L556 112 C380 148 180 196 0 205 Z" fill="var(--brand-grey)"/>
      <path d="M0 208 C180 200 380 152 556 118 L556 342 L0 342 Z" fill="var(--brand-blue)"/>
    </svg>

    <div class="brand-name">Harborview Nest<small>ADVISORS, LLC</small></div>

    <div class="contact">
      <div class="contact__fax">Toll Free Fax: (800) 555-0193</div>
      <div class="contact__row">(555) 318-2946
        <svg class="contact__icon" viewBox="0 0 24 24" aria-hidden="true"><path d="M6.6 10.8a15.1 15.1 0 0 0 6.6 6.6l2.2-2.2a1 1 0 0 1 1-.25 11.4 11.4 0 0 0 3.6.57 1 1 0 0 1 1 1V20a1 1 0 0 1-1 1A17 17 0 0 1 3 4a1 1 0 0 1 1-1h3.5a1 1 0 0 1 1 1c0 1.25.2 2.45.57 3.57a1 1 0 0 1-.25 1z"/></svg>
      </div>
      <div class="contact__row">gpelham@harborviewnest.example
        <svg class="contact__icon" viewBox="0 0 24 24" aria-hidden="true"><path d="M2 5h20v14H2z"/><path d="M3 6l9 7 9-7" fill="none" stroke="var(--brand-blue)" stroke-width="2"/></svg>
      </div>
    </div>

    <div class="person">
      <div class="person__name">Gregor Pelham, <span>MBA, ChFC®, CLU®</span></div>
      <div class="person__role">Financial Advisor</div>
      <div class="person__role">Registered Representative</div>
    </div>

    <div class="rule-line">2187 Meadowlark Ridge Rd. Suite K418 Virginia Beach, VA 23999</div>
  </section>

  <section class="card card--back" aria-label="Business card back">
    <div class="back-mark">Harborview Nest<br>Advisors</div>
    <p class="disclosure">Gregor Pelham is a registered representative of and offers securities through Brightmoor Capital Brokerage Corporation, Member FNQX. Brightmoor Capital Brokerage Corporation is a member of the Brightmoor Capital Alliance which is the marketing name for Brightmoor Holding Corporation and its affiliates.</p>
    <div class="rule-line">Turning Your Earned Income Into Retirement Income</div>
  </section>

</main>
</body>
</html>
```